Indy Film Production Company/Studio

We need a business card designed from an existing logo. We are a digital studio/production company that caters to creating genre entertainment, like Action, Horror, and martial arts. The card along with the logo will be used to Brand the company from letter heads to banners. The design will also be used for postcards and Brochures. It should be professional and masculine.
Updates

Thank you to all the designers who have participated. I'm narrowing down who it will be. Thank you again.

Target Market(s)

Investors, Networks, Producers, and actors

Industry/Entity Type

Film Production

Contact Information for Business Card

Teodoro Valbuena
Producer/Writer/Director
www.kestrelpicturehouse.example

Requirements
Must have
• Website address, Facebook icon and Twitter icon possibly in the back of the card.
Nice to have
• Logline of Company: Follow The Action.

```html
<!DOCTYPE html>
<html lang="en">
<head>
<meta charset="utf-8">
<title>Kestrel Picture House – Business Card</title>
<link href="https://fonts.googleapis.com/css2?family=Questrial&display=swap" rel="stylesheet">
<style>
  :root {
    --backdrop: #2b2826;
    --card: #141414;
    --card-edge: #1f1f1f;
    --silver: #c9c9c9;
    --text-soft: #8d8d8d;
    --text-main: #a9a9a9;
    --photo-dark: #1c1c1c;
    --photo-light: #8a8a8a;
  }
  * { margin: 0; padding: 0; box-sizing: border-box; }
  html, body {
    width: 1200px; height: 727px; overflow: hidden;
    background: var(--backdrop);
    font-family: "Questrial", "Century Gothic", sans-serif;
  }
  .stage {
    position: relative; width: 1200px; height: 727px;
    display: flex; align-items: center; justify-content: center; gap: 40px;
  }
  .card {
    position: relative; width: 540px; height: 309px;
    background: var(--card);
    border: 1px solid var(--card-edge);
    border-radius: 6px;
    overflow: hidden;
  }
  .brand-name {
    color: var(--silver);
    font-weight: 400;
    letter-spacing: 0.04em;
    text-transform: uppercase;
    line-height: 1.1;
  }

  /* Front */
  .card-front .brand-name {
    position: absolute; left: 0; right: 0; top: 90px;
    text-align: center; font-size: 40px;
  }
  .card-front .website {
    position: absolute; left: 0; right: 0; top: 190px;
    text-align: center; font-size: 15px; color: var(--text-soft);
  }
  .social-squares {
    position: absolute; right: 30px; bottom: 28px;
    display: flex; gap: 6px;
  }
  .social-squares span {
    width: 16px; height: 16px; background: var(--text-soft); border-radius: 2px;
  }

  /* Back */
  .card-back .brand-name {
    position: absolute; left: 150px; top: 30px; font-size: 24px;
  }
  .contact {
    position: absolute; left: 30px; top: 104px; z-index: 1;
    color: var(--text-soft); font-size: 13px; line-height: 1.5;
  }
  .contact .person { color: var(--text-main); font-size: 20px; }
  .contact .role { font-size: 15px; margin-bottom: 4px; }
  .contact .row { display: flex; align-items: center; gap: 6px; white-space: nowrap; }
  .contact .row + .row { margin-top: 1px; }
  .contact svg { width: 13px; height: 13px; fill: var(--text-soft); flex: none; }
  .contact .pair { display: flex; gap: 14px; }
  .camera-photo {
    position: absolute; right: 0; bottom: 0; width: 145px; height: 165px;
    background: radial-gradient(ellipse at 55% 55%, var(--photo-light) 0%, #4a4a4a 40%, var(--photo-dark) 78%, var(--card) 100%);
  }
</style>
</head>
<body>
<main class="stage">
  <section class="card card-front">
    <div class="brand-name">Kestrel<br>Picture House</div>
    <div class="website">www.kestrelpicturehouse.example</div>
    <div class="social-squares"><span></span><span></span><span></span></div>
  </section>

  <section class="card card-back">
    <div class="brand-name">Kestrel Picture House</div>
    <div class="contact">
      <div class="person">Teodoro Valbuena</div>
      <div class="role">Producer/Writer/Director</div>
      <div class="pair">
        <div class="row">
          <svg viewBox="0 0 16 16" aria-hidden="true"><path d="M2 5c0-2 2-3 6-3s6 1 6 3v1h-3V5H5v1H2zM4 7h8l2 6H2z"/></svg>
          <span>000 000 0000</span>
        </div>
        <div class="row">
          <svg viewBox="0 0 16 16" aria-hidden="true"><path d="M1 3h14v10H1zM2 4l6 5 6-5v1L8 10 2 5z" fill-rule="evenodd"/></svg>
          <span>info@kestrelpicturehouse.example</span>
        </div>
      </div>
      <div class="row">https://social.example/kestrelpicture</div>
      <div class="row">www.network.example/kestrelpicture</div>
    </div>
    <div class="camera-photo" role="img" aria-label="Photograph of a professional cinema camera rig"></div>
  </section>
</main>
</body>
</html>
```